Business Card & Letterhead Design

We a financial advice company based in Australia. We provide advice to wealthy farmers.

We are changing our business name FROM Brightvale Financial TO Tallowmere Wealth and we need a new letterhead and double sided business card design

Attached is designs from our previous branding (Brightvale Financial) as it includes all the details we require on the new Tallowmere Wealth business cards and letterhead.

Need extra days to review

```html
<!DOCTYPE html>
<html lang="en">
<head>
<meta charset="utf-8">
<title>Tallowmere Wealth Letterhead</title>
<link href="https://fonts.googleapis.com/css2?family=Source+Sans+3:wght@400;600&display=swap" rel="stylesheet">
<style>
  :root {
    --ink: #3d4449;
    --slate: #5c6970;
    --charcoal: #404040;
    --watermark: #dfdedd;
    --paper: #ffffff;
  }
  * { margin: 0; padding: 0; box-sizing: border-box; }
  html, body { width: 1200px; height: 1000px; overflow: hidden; background: var(--paper); }
  body { font-family: "Source Sans 3", sans-serif; color: var(--ink); position: relative; }
  .letterhead { position: absolute; left: 245px; top: 0; width: 713px; height: 1000px; background: var(--paper); }
  .brand { position: absolute; left: 48px; top: 52px; width: 220px; text-align: center; }
  .brand-mark { display: block; margin: 0 auto 6px; }
  .brand-name { font-size: 21px; font-weight: 400; letter-spacing: 0.5px; text-transform: uppercase; line-height: 1; color: var(--ink); }
  .brand-tagline { font-size: 8.5px; letter-spacing: 3.2px; text-transform: uppercase; color: #7d868b; margin-top: 1px; }
  .divider { position: absolute; top: 45px; width: 2px; height: 104px; background: var(--ink); }
  .divider--first { left: 301px; }
  .divider--second { left: 475px; }
  .legal { position: absolute; font-size: 11.5px; line-height: 15.2px; color: var(--ink); white-space: nowrap; }
  .legal--representative { left: 322px; top: 42px; font-size: 11.2px; }
  .legal--licensee { left: 497px; top: 50px; }
  .header-band { position: absolute; left: 0; top: 158px; }
  .watermark { position: absolute; left: 93px; top: 272px; }
  .contact { position: absolute; top: 873px; font-size: 11.5px; line-height: 14.2px; color: #2e3336; white-space: nowrap; }
  .contact--address { left: 133px; }
  .contact--phone { left: 427px; }
  .footer-band { position: absolute; left: 0; top: 937px; width: 713px; height: 63px; background: var(--slate); color: var(--paper); font-size: 17px; font-weight: 600; text-align: center; line-height: 58px; }
</style>
</head>
<body>
<main class="letterhead">
  <header>
    <div class="brand">
      <svg class="brand-mark" width="60" height="60" viewBox="0 0 60 60" aria-hidden="true">
        <circle cx="30" cy="30" r="27.5" fill="none" stroke="var(--ink)" stroke-width="2.5"/>
      </svg>
      <div class="brand-name">Tallowmere Wealth</div>
      <div class="brand-tagline">Strategic Financial Advice</div>
    </div>
    <span class="divider divider--first"></span>
    <p class="legal legal--representative">Kestrel Investments Pty Ltd<br>ATF The Glenmore Investment<br>Trust T/AS Brightvale Financial<br>ABN: 41 208 613 557<br>Corporate Authorised<br>Representative of Meridian<br>Financial Planning Limited</p>
    <span class="divider divider--second"></span>
    <p class="legal legal--licensee">Meridian Financial Planning Limited<br>ABN 62 005 318 420<br>Australian Financial Services Licence<br>Licence Number 318 402<br>Principle Address: 410 Harbour St<br>PO Box 1942 Melbourne VIC 3001</p>
    <svg class="header-band" width="713" height="16" viewBox="0 0 713 16" aria-hidden="true">
      <polygon points="0,0 293,0 276,16 0,16" fill="var(--slate)"/>
      <polygon points="283,16 300,0 465,0 448,16" fill="var(--charcoal)"/>
      <polygon points="455,16 472,0 713,0 713,16" fill="var(--charcoal)"/>
    </svg>
  </header>

  <svg class="watermark" width="528" height="530" viewBox="0 0 528 530" aria-hidden="true">
    <circle cx="263" cy="265" r="259" fill="none" stroke="var(--watermark)" stroke-width="8"/>
    <text x="263" y="283" text-anchor="middle" font-family="Source Sans 3, sans-serif" font-size="50" font-weight="400" fill="var(--watermark)">Tallowmere Wealth</text>
  </svg>

  <footer>
    <p class="contact contact--address">Suite 4A, 18 Wexley St<br>Kangaroo Point QLD 4169<br>PO Box 5120<br>East Brisbane QLD 4169</p>
    <p class="contact contact--phone">p (07) 3000 1284<br>f (07) 3000 5671<br>www.brightvalefinancial.com.au<br>admin@brightvalefinancial.com.au</p>
    <div class="footer-band">'Financial peace of mind'</div>
  </footer>
</main>
</body>
</html>
```